Business Card Design

Want something very unique. No business, just personal. The image I submitted is for inspiration only.

Target Market(s)

friends and new acquaintances

Industry/Entity Type

Business

Contact Information for Business Card

Dora Malcott
Santa Fe, NM
505-718-2946
doramalcott@quellmail.net

```html
<!DOCTYPE html>
<html lang="en">
<head>
<meta charset="utf-8">
<title>Dora Malcott – Personal Card</title>
<link href="https://fonts.googleapis.com/css2?family=Libre+Baskerville:wght@400;700&display=swap" rel="stylesheet">
<style>
  :root {
    --bg: #ecebe8;
    --paper: #ffffff;
    --ink: #231f20;
    --gold: #f0ae1a;
    --light: #ffffff;
    --shadow: rgba(0,0,0,0.18);
  }
  html, body {
    margin: 0;
    padding: 0;
    width: 1200px;
    height: 504px;
    overflow: hidden;
    background: var(--bg);
  }
  .stage {
    position: relative;
    width: 1200px;
    height: 504px;
  }
  .card {
    position: absolute;
    top: 87px;
    width: 530px;
    height: 330px;
    border-radius: 26px;
    overflow: hidden;
    box-shadow: 0 6px 18px var(--shadow);
    background: var(--paper);
    font-family: "Libre Baskerville", Georgia, serif;
  }
  .card--front { left: 50px; }
  .card--back { left: 620px; }
  .front-waves {
    position: absolute;
    inset: 0;
    width: 530px;
    height: 330px;
  }
  .name {
    position: absolute;
    left: 30px;
    top: 84px;
    margin: 0;
    font-size: 36px;
    font-weight: 400;
    color: var(--ink);
    letter-spacing: 0.5px;
  }
  .name__first { color: var(--gold); }
  .location {
    position: absolute;
    left: 40px;
    top: 190px;
    margin: 0;
    display: flex;
    align-items: center;
    gap: 6px;
    font-size: 14px;
    color: var(--ink);
  }
  .contact {
    position: absolute;
    right: 26px;
    top: 188px;
    text-align: right;
    color: var(--light);
    font-size: 14px;
    line-height: 1;
  }
  .contact__row {
    display: flex;
    justify-content: flex-end;
    align-items: center;
    gap: 6px;
    margin-bottom: 16px;
    white-space: nowrap;
  }
  .follow {
    display: flex;
    justify-content: flex-end;
    align-items: center;
    gap: 8px;
    font-size: 12px;
    white-space: nowrap;
  }
  .network {
    font-size: 11px;
    color: var(--light);
  }
  .photo {
    position: absolute;
    inset: 0;
    background:
      radial-gradient(ellipse at 30% 75%, #c9b9a0 0%, rgba(201,185,160,0) 45%),
      radial-gradient(ellipse at 75% 70%, #b49a6c 0%, rgba(180,154,108,0) 50%),
      linear-gradient(160deg, #cfc7b4 0%, #8d7a63 45%, #6f5b45 70%, #a08658 100%);
  }
</style>
</head>
<body>
<main class="stage">
  <section class="card card--front">
    <svg class="front-waves" viewBox="0 0 530 330" aria-hidden="true">
      <path d="M0,300 C140,300 210,250 270,190 C330,130 420,112 530,108 L530,330 L0,330 Z" fill="var(--ink)"/>
      <path d="M0,268 C140,272 200,222 262,160 C325,98 420,80 530,76 L530,94 C420,98 330,116 268,176 C205,238 140,288 0,286 Z" fill="var(--gold)"/>
      <path d="M0,294 C140,296 206,246 266,184 C326,124 420,104 530,101" fill="none" stroke="var(--ink)" stroke-width="3"/>
      <path d="M20,318 C130,318 190,298 232,272" fill="none" stroke="var(--light)" stroke-width="2"/>
    </svg>

    <h1 class="name"><span class="name__first">Dora</span> Malcott</h1>

    <p class="location">
      <svg width="12" height="16" viewBox="0 0 12 16" aria-hidden="true">
        <path d="M6,0 C2.7,0 0,2.6 0,5.8 C0,10 6,16 6,16 C6,16 12,10 12,5.8 C12,2.6 9.3,0 6,0 Z M6,8.3 C4.6,8.3 3.5,7.2 3.5,5.8 C3.5,4.4 4.6,3.3 6,3.3 C7.4,3.3 8.5,4.4 8.5,5.8 C8.5,7.2 7.4,8.3 6,8.3 Z" fill="var(--ink)"/>
      </svg>
      Santa Fe, NM
    </p>

    <div class="contact">
      <div class="contact__row">
        <svg width="13" height="13" viewBox="0 0 14 14" aria-hidden="true">
          <circle cx="7" cy="7" r="6.2" fill="none" stroke="var(--light)" stroke-width="1.3"/>
          <path d="M4.6,3.6 L6,3.4 L6.6,5.2 L5.8,6 C6.2,7 7,7.8 8,8.2 L8.8,7.4 L10.6,8 L10.4,9.4 C8,10 4,6 4.6,3.6 Z" fill="var(--light)"/>
        </svg>
        505-718-2946
      </div>
      <div class="contact__row">
        <svg width="13" height="11" viewBox="0 0 14 11" aria-hidden="true">
          <rect x="0.6" y="0.6" width="12.8" height="9.8" rx="1" fill="none" stroke="var(--light)" stroke-width="1.2"/>
          <path d="M0.8,1 L7,6 L13.2,1" fill="none" stroke="var(--light)" stroke-width="1.2"/>
        </svg>
        doramalcott@quellmail.net
      </div>
      <div class="follow">
        <span>Follow Us On</span>
        <span class="network">Friendloop</span>
        <span class="network">Chirpline</span>
        <span class="network">Worknet</span>
      </div>
    </div>
  </section>

  <section class="card card--back">
    <div class="photo" role="img" aria-label="Photograph of two people crouching beside a group of resting cheetahs in a sunny enclosure with rocks and a wire fence"></div>
  </section>
</main>
</body>
</html>
```